Shopify Web-Page "Tiny-ThreadDays

We are building a new business in Switzerland offering premium sewing holiday camps for kids aged 9–14. In enclosed brief outlines our requirements for a complete Shopify homepage design and a multilingual logo creation.
Domains: tiny-threaddays.ch ; tiny-giornifilo.ch ; tiny-fadentage.ch

Project Overview
We are looking for:
1. A modern, fully designed Shopify homepage in English using standard Shopify content blocks (no custom coding), which we can later update ourselves. Supporting Multilanguage (EN, German, Italian).

2. A logo design that includes the brand identity and communicates our multilingual, creative, and child-focused positioning.

All details in enclosed

```html
<!DOCTYPE html>
<html lang="en">
<head>
<meta charset="utf-8">
<title>Tiny-ThreadDays – Creative Sewing Holidays for Kids</title>
<link href="https://fonts.googleapis.com/css2?family=Fredoka:wght@400;500;600&family=Mali:wght@400;500;600&family=Gochi+Hand&display=swap" rel="stylesheet">
<style>
:root{
  --yellow:#f2c21a;
  --pink:#e8365d;
  --pink-soft:#ee5b78;
  --blue:#2a8fd6;
  --purple:#2f1cbb;
  --deep:#3b1f86;
  --green:#a2d63b;
  --orange:#f4a41c;
  --ink:#2b2a4c;
  --muted:#55546e;
  --line:#e3e1ee;
  --white:#fff;
}
*{box-sizing:border-box;margin:0;padding:0}
html,body{width:1200px;height:5042px;overflow:hidden}
body{position:relative;background:var(--white);font-family:"Mali",cursive;color:var(--ink)}
.abs{position:absolute}
.display{font-family:"Fredoka",sans-serif}
.eyebrow{font-family:"Gochi Hand",cursive;color:var(--yellow);font-size:19px}
.section-title{font-family:"Fredoka",sans-serif;font-weight:600;font-size:33px;color:var(--blue)}
.section-title .accent{color:var(--pink)}
.center{left:0;width:1200px;text-align:center}
.btn{display:inline-block;border-radius:8px;font-size:13px;padding:7px 18px;color:#fff;box-shadow:3px 3px 0 rgba(0,0,0,.25);white-space:nowrap}
.btn-pink{background:var(--pink)}
.btn-deep{background:var(--deep)}
.photo{border-radius:0}

/* top bar & nav */
.topbar{top:0;left:0;width:1200px;height:40px;background:var(--yellow);font-size:12px;color:var(--ink)}
.topbar span{position:absolute;top:12px}
.nav{top:40px;left:0;width:1200px;height:72px;background:#fff}
.brand{position:absolute;top:23px;left:141px;display:flex;align-items:center;gap:8px;font-family:"Fredoka",sans-serif;font-weight:600;font-size:21px;color:var(--pink)}
.brand i{display:block;width:16px;height:16px;border-radius:50%;background:var(--pink)}
.nav a{position:absolute;top:27px;font-size:13px;color:var(--ink);text-decoration:none}
.nav a.active{color:var(--pink)}
.nav .btn{top:17px;left:946px;color:#fff}

/* hero */
.hero{top:112px;left:0;width:1200px;height:520px;background:linear-gradient(180deg,#8b6a4f 0%,#b98a5e 45%,#6c4b38 100%)}
.hero h1{top:285px;font-family:"Fredoka",sans-serif;font-weight:600;font-size:50px;color:#fff;text-shadow:0 2px 8px rgba(0,0,0,.35)}
.hero p{top:352px;font-size:17px;color:#fff;text-shadow:0 1px 4px rgba(0,0,0,.4)}
.hero-wave{top:480px;left:0}

/* about */
.about-img{top:744px;left:142px;width:400px;height:370px;border-radius:40px;background:linear-gradient(135deg,#d9c3b0,#e9a7b5)}
.badge-photo{border-radius:50%;background:linear-gradient(135deg,#c89a84,#8c5e4c);border:5px solid #fff}
.person-tag{font-family:"Gochi Hand",cursive;color:var(--ink);font-size:16px}
.person-role{font-size:10px;color:var(--muted)}
.about-text{top:784px;left:642px;width:430px}
.about-text h2{margin-top:4px}
.about-text h3{font-weight:500;font-size:15px;color:var(--pink);margin:16px 0 10px}
.about-text p{font-size:12px;line-height:23px;color:var(--ink)}
.about-text .btn{margin-top:24px}

/* how it works */
.how{top:1252px;left:0;width:1200px;height:600px;background:var(--purple)}
.how-card{top:190px;width:167px;height:314px;border-radius:14px;background:rgba(255,255,255,.08);border:1px solid rgba(255,255,255,.18);text-align:center;color:#fff;padding:28px 14px 0}
.how-card .ico{width:80px;height:80px;border-radius:50%;margin:0 auto 18px}
.how-card h4{font-family:"Fredoka",sans-serif;font-weight:500;font-size:15px;line-height:19px;margin-bottom:12px}
.how-card p{font-size:11.5px;line-height:23px;opacity:.95}

/* why parents */
.why-blob{top:1830px;left:640px;width:560px;height:560px;background:var(--purple);border-radius:60% 0 0 40%}
.why-img{top:1900px;left:660px;width:540px;height:500px;border-radius:50% 0 0 0;background:linear-gradient(150deg,#e7c9a6,#cfa58a 50%,#f0e4da)}
.why-title{top:1942px;left:143px}
.why-item{width:220px;font-size:14px;line-height:22px;padding-left:28px;padding-bottom:10px;border-bottom:1px dashed #d9d6e6}
.why-item::before{content:"";position:absolute;left:2px;top:5px;width:11px;height:11px;background:var(--orange);transform:rotate(45deg)}

/* green band */
.join{top:2410px;left:0;width:1200px;height:205px;background:var(--green)}
.join h2{top:64px;font-family:"Mali",cursive;font-weight:500;font-size:29px;color:var(--ink)}
.join .btns{top:124px;display:flex;justify-content:center;gap:18px}

/* camps */
.camp-card{top:2812px;width:289px;text-align:center}
.camp-img{height:190px;border-radius:36px;background:linear-gradient(135deg,#d8b898,#c28d79 55%,#e8dccd)}
.camp-card h4{font-family:"Mali",cursive;font-weight:500;font-size:15px;margin:18px 0 8px}
.camp-card p{font-size:11.5px;line-height:23px;color:var(--ink);padding:0 30px}
.camp-meta{display:flex;justify-content:space-between;margin:12px 20px 0;padding:6px 8px;border-top:1px solid var(--line);border-bottom:1px solid var(--line);font-size:12px}
.camp-meta b{font-weight:500;color:var(--pink);font-size:15px}
.camp-dates{font-size:12px;margin:10px 0 14px}

/* orange band */
.ready{top:3366px;left:0;width:1200px;height:324px;background:var(--orange)}
.ready h2{top:84px;font-family:"Mali",cursive;font-weight:500;font-size:31px;color:#fff}
.ready p{top:134px;font-size:13px;line-height:22px;color:#fff}
.ready .btn{top:210px;left:498px}

/* faq */
.faq{height:42px;width:436px;border:1px solid var(--line);border-radius:8px;display:flex;align-items:center;font-size:14px;box-shadow:0 2px 4px rgba(0,0,0,.05)}
.faq .n{width:28px;height:28px;margin:0 12px 0 4px;border-radius:6px;background:var(--deep);color:#fff;font-size:13px;display:flex;align-items:center;justify-content:center}
.faq .plus{margin-left:auto;margin-right:16px;color:var(--pink);font-size:17px}
.faq.open{border-color:var(--deep);border-width:2px}
.faq-answer{top:3984px;left:662px;width:390px;font-size:14px;line-height:28px}

/* cta */
.cta-img{top:4266px;left:0;width:590px;height:440px;background:linear-gradient(135deg,#d9b99c,#b88a74 50%,#f2ece6)}
.cta-circle{top:4300px;left:556px;width:520px;height:380px;border-radius:50%;background:var(--pink-soft);border:2px dashed rgba(255,255,255,.6);color:#fff;text-align:center}
.cta-circle h2{font-family:"Mali",cursive;font-weight:500;font-size:31px;margin-top:118px}
.cta-circle p{font-size:14px;line-height:22px;margin:14px 60px 18px}

/* footer */
.footer{top:4660px;left:0;width:1200px;height:382px}
.foot-brand{top:4752px;left:141px;width:130px;height:126px;border-radius:6px;background:#fff;display:flex;align-items:center;justify-content:center;text-align:center;font-family:"Fredoka",sans-serif;font-weight:600;font-size:17px;line-height:20px;color:var(--pink)}
.social{top:4897px;width:22px;height:22px;border-radius:50%;border:1px solid var(--orange)}
.foot-col{top:4747px;color:#fff}
.foot-col h5{font-family:"Mali",cursive;font-weight:600;font-size:15px;margin-bottom:16px}
.foot-col li{list-style:none;font-size:12px;line-height:25px}
.contact-row{display:flex;gap:14px;font-size:12px;line-height:17px;margin-bottom:14px}
.contact-row svg{flex:none;margin-top:2px}
.email-field{width:256px;height:34px;border-radius:6px;background:#fff;color:#777;font-size:11px;padding:10px 12px;margin:12px 0 10px}
.copy{top:5008px;font-size:12px;color:#fff}
</style>
</head>
<body>

<!-- top bar -->
<div class="abs topbar">
  <span style="left:668px">☏ +41 44 555 01 90</span>
  <span style="left:808px">➤ hello@tiny-threaddays.ch</span>
  <span style="left:990px">Eng ▾</span>
</div>

<!-- navigation -->
<header class="abs nav">
  <div class="brand"><i></i>Tiny-ThreadDays</div>
  <a class="active" style="left:392px">Home</a>
  <a style="left:467px">About Us</a>
  <a style="left:566px">Camps</a>
  <a style="left:645px">How It Works</a>
  <a style="left:775px">Faq</a>
  <a style="left:838px">Contact Us</a>
  <span class="abs btn btn-pink">Book Now ➔</span>
</header>

<!-- hero -->
<section class="abs hero" role="img" aria-label="Group of smiling children holding up their colourful sewn fabric pieces in a bright workshop"></section>
<h1 class="abs center" style="top:397px;font-family:'Fredoka',sans-serif;font-weight:600;font-size:50px;color:#fff;text-shadow:0 2px 8px rgba(0,0,0,.35)">Creative Sewing Holidays for Kids</h1>
<p class="abs center" style="top:464px;font-size:17px;color:#fff;text-shadow:0 1px 4px rgba(0,0,0,.4)">Professional instruction in small groups. Multilingual support. Real results. Ages 9–14 in Zurich.</p>
<svg class="abs hero-wave" width="1200" height="160" viewBox="0 0 1200 160">
  <path d="M0 70 C200 20 380 60 560 60 C760 60 900 10 1200 40 L1200 160 L0 160Z" fill="#ef9fb6"/>
  <path d="M0 100 C220 40 420 80 600 90 C820 100 960 60 1200 90 L1200 160 L0 160Z" fill="#8fd0f0"/>
  <path d="M0 95 C240 70 420 150 640 130 C860 110 1000 40 1200 70 L1200 160 L0 160Z" fill="#c9a42a"/>
  <path d="M0 118 C260 90 430 160 660 150 C880 140 1020 80 1200 100 L1200 160 L0 160Z" fill="#fff"/>
</svg>

<!-- about -->
<div class="abs about-img" role="img" aria-label="Girl sewing fabric on a machine in a sunny workshop"></div>
<div class="abs badge-photo" style="top:852px;left:435px;width:92px;height:92px" role="img" aria-label="Portrait of sewing expert Lena"></div>
<div class="abs person-tag" style="top:990px;left:518px">Lena</div>
<div class="abs person-role" style="top:1016px;left:518px">Sewing Expert</div>
<div class="abs badge-photo" style="top:1052px;left:363px;width:100px;height:100px" role="img" aria-label="Portrait of design specialist Mara"></div>
<div class="abs person-tag" style="top:1117px;left:308px">Mara</div>
<div class="abs person-role" style="top:1146px;left:252px">Design Specialist</div>

<div class="abs about-text">
  <div class="eyebrow">What We Do</div>
  <h2 class="section-title">About Tiny-<span class="accent">ThreadDays</span></h2>
  <h3>Creative Learning with Fun &amp; Structure</h3>
  <p>Lena and Mara have over 10 years of experience in teaching children sewing, tailoring, and design with fun, style, and structure.<br>
  In small groups (max. 8 children), we guide young talents through a creative week of vacation – with real results: self-sewn pieces, new friends, and lots of pride.<br>
  At the last day, the children show off their success, their own sewn unique pieces, in a sympathetic fashion show.</p>
  <span class="btn btn-deep">Read More ➔</span>
</div>

<!-- how it works -->
<section class="abs how">
  <div class="abs eyebrow center" style="top:100px">Holiday camp</div>
  <h2 class="abs section-title center" style="top:118px;color:#4fb3f0">How Our <span class="accent">Camps Work</span></h2>
  <div class="abs how-card" style="left:143px"><div class="ico" style="background:#9ed34a"></div><h4>Project<br>Selection</h4><p>Your child chooses their own model based on previously produced clothing items and sewing patterns.</p></div>
  <div class="abs how-card" style="left:327px"><div class="ico" style="background:#e8455d"></div><h4>Fabric<br>selection</h4><p>High-quality fabrics are available for your child to choose from for their unique creation.</p></div>
  <div class="abs how-card" style="left:515px"><div class="ico" style="background:#3aa0e8"></div><h4>Sewing Machine<br>Operation</h4><p>Learn how to use a sewing machine with our top-quality Stitchwell machines.</p></div>
  <div class="abs how-card" style="left:699px"><div class="ico" style="background:#f27aa8"></div><h4>Sewing<br>&amp; Refining</h4><p>Step by step to the goal with professional guidance from our experienced instructors.</p></div>
  <div class="abs how-card" style="left:887px"><div class="ico" style="background:#ea4a5c"></div><h4>Camps Work<br>Showtime!</h4><p>Fashion show or photo shoot at the end of the week to showcase their creations.</p></div>
</section>
<svg class="abs" style="top:1236px;left:0" width="1200" height="24" viewBox="0 0 1200 24"><path d="M0 24 L0 12 Q50 4 100 12 T200 10 T300 14 T400 8 T500 12 T600 9 T700 13 T800 8 T900 12 T1000 9 T1100 13 T1200 10 L1200 24Z" fill="var(--purple)"/></svg>

<!-- why parents -->
<div class="abs why-blob"></div>
<div class="abs why-img" role="img" aria-label="Smiling instructor helping children sewing at machines"></div>
<div class="abs why-title">
  <div class="eyebrow">Parents Trust Us</div>
  <h2 class="section-title">Why Parents <span class="accent">Choose Us</span></h2>
</div>
<div class="abs why-item" style="top:2030px;left:143px">Small groups &amp; personalized attention</div>
<div class="abs why-item" style="top:2030px;left:376px">Multilingual supervision (DE / EN / IT)</div>
<div class="abs why-item" style="top:2104px;left:143px">High-quality fabrics &amp; top-quality sewing machines (Stitchwell)</div>
<div class="abs why-item" style="top:2104px;left:376px">Encouragement of creativity, self-confidence, and fine motor skills</div>
<div class="abs why-item" style="top:2200px;left:143px;border:none">Safe, loving environment in Zurich, various places easy to reach</div>
<div class="abs why-item" style="top:2200px;left:376px;border:none">Pick-up Service from the Main-Station</div>

<!-- join band -->
<section class="abs join">
  <svg class="abs" style="top:-30px;left:0" width="1200" height="60" viewBox="0 0 1200 60"><path d="M0 60 L0 20 C300 50 700 0 1200 30 L1200 60Z" fill="var(--green)"/></svg>
  <h2 class="abs center">Join the Stitching Fun This Holiday!"</h2>
  <div class="abs btns center"><span class="btn btn-deep">View Upcoming Camps ➔</span><span class="btn btn-pink">Book Now ➔</span></div>
</section>

<!-- upcoming camps -->
<div class="abs eyebrow center" style="top:2710px">Sewing Adventures</div>
<h2 class="abs section-title center" style="top:2730px">Upcoming <span class="accent">Camps</span></h2>
<article class="abs camp-card" style="left:141px">
  <div class="camp-img" role="img" aria-label="Children sewing spring projects with an instructor"></div>
  <h4>Spring Sewing Camp</h4>
  <p>Join us for a creative week during spring break! Children will learn sewing basics and create their own spring-themed projects.</p>
  <div class="camp-meta"><span>Age: 9-14</span><b>CHF 450</b></div>
  <div class="camp-dates">Dates: April 10-26</div>
  <span class="btn btn-pink">Book Now ➔</span>
</article>
<article class="abs camp-card" style="left:456px">
  <div class="camp-img" role="img" aria-label="Kids creating summer clothing in the workshop"></div>
  <h4>Summer Fashion Camp</h4>
  <p>Our popular summer program where kids design and create their own summer wardrobe items in a fun, supportive environment.</p>
  <div class="camp-meta"><span>Age: 9-14</span><b>CHF 450</b></div>
  <div class="camp-dates">Dates: April 10-26</div>
  <span class="btn btn-pink">Book Now ➔</span>
</article>
<article class="abs camp-card" style="left:769px">
  <div class="camp-img" role="img" aria-label="Group of children at sewing machines making autumn accessories"></div>
  <h4>Autumn Creative Camp</h4>
  <p>Get ready for cooler weather by creating cozy autumn accessories and clothing items in this creative camp.</p>
  <div class="camp-meta"><span>Age: 9-14</span><b>CHF 450</b></div>
  <div class="camp-dates">Dates: April 10-26</div>
  <span class="btn btn-pink">Book Now ➔</span>
</article>

<!-- ready band -->
<section class="abs ready">
  <svg class="abs" style="top:-14px;left:0" width="1200" height="24" viewBox="0 0 1200 24"><path d="M0 24 L0 12 Q60 4 120 12 T240 10 T360 14 T480 8 T600 12 T720 9 T840 13 T960 8 T1080 12 T1200 10 L1200 24Z" fill="var(--orange)"/></svg>
  <h2 class="abs center">Ready for a Creative Adventure?</h2>
  <p class="abs center">Spaces are limited to 8 children per camp to ensure personalized attention.<br>Book now to secure your child's spot!</p>
  <span class="abs btn btn-deep">View All Camps &amp; Book ➔</span>
</section>

<!-- faq -->
<div class="abs eyebrow center" style="top:3776px">Answers You're Looking For</div>
<h2 class="abs section-title center" style="top:3794px">Frequently <span class="accent">Asked Questions</span></h2>
<div class="abs faq" style="top:3869px;left:143px"><span class="n">01</span>Does my child need any prior knowledge?<span class="plus">+</span></div>
<div class="abs faq" style="top:3926px;left:143px"><span class="n">02</span>How does the pick-up service work?<span class="plus">+</span></div>
<div class="abs faq" style="top:3983px;left:143px"><span class="n">03</span>How many items of clothing are produced?<span class="plus">+</span></div>
<div class="abs faq" style="top:4040px;left:143px"><span class="n">04</span>What should my child bring to camp?<span class="plus">+</span></div>
<div class="abs faq" style="top:4099px;left:143px"><span class="n">05</span>What are the camp hours?<span class="plus">+</span></div>
<div class="abs faq" style="top:4156px;left:143px"><span class="n">06</span>What safety measures are in place?<span class="plus">+</span></div>
<div class="abs faq" style="top:3869px;left:618px"><span class="n">07</span>What is your cancellation policy?<span class="plus">+</span></div>
<div class="abs faq open" style="top:3926px;left:618px"><span class="n">08</span>Do children need any prior sewing experience?<span class="plus">–</span></div>
<p class="abs faq-answer">No prior experience is necessary! Our expert instructors will teach everything from basic machine operation to advanced techniques, all tailored to each child's skill level.</p>
<div class="abs faq" style="top:4099px;left:618px"><span class="n">09</span>What do children take home?<span class="plus">+</span></div>
<div class="abs faq" style="top:4158px;left:618px"><span class="n">10</span>Where are the camps located?<span class="plus">+</span></div>

<!-- cta -->
<div class="abs cta-img" role="img" aria-label="Mother and daughter smiling while sewing together at a machine"></div>

<!-- footer -->
<svg class="abs footer" width="1200" height="382" viewBox="0 0 1200 382"><path d="M0 40 C200 10 420 60 620 30 C820 0 1000 40 1200 10 L1200 382 L0 382Z" fill="var(--deep)"/></svg>
<div class="abs cta-circle">
  <h2>Ready to Start Creating?</h2>
  <p>Join our community of young designers and watch your child's creativity flourish!</p>
  <span class="btn btn-deep">View All Camps &amp; Book ➔</span>
</div>

<div class="abs foot-brand">Tiny-<br>ThreadDays</div>
<span class="abs social" style="left:143px"></span>
<span class="abs social" style="left:175px"></span>
<span class="abs social" style="left:207px"></span>
<span class="abs social" style="left:239px"></span>

<div class="abs foot-col" style="left:350px">
  <h5>Quick Links</h5>
  <ul><li>Home</li><li>About Us</li><li>Camps</li><li>How It Works</li><li>Faq</li><li>Contact Us</li></ul>
</div>
<div class="abs foot-col" style="left:520px;width:220px">
  <h5>Contact Details</h5>
  <div class="contact-row"><svg width="16" height="16" viewBox="0 0 16 16"><path d="M8 1a5 5 0 0 0-5 5c0 4 5 9 5 9s5-5 5-9a5 5 0 0 0-5-5zm0 7a2 2 0 1 1 0-4 2 2 0 0 1 0 4z" fill="#fff"/></svg><span>Nählweg 12,<br>8004 Zürich</span></div>
  <div class="contact-row"><svg width="16" height="16" viewBox="0 0 16 16"><path d="M4 1l3 3-2 2c1 2 3 4 5 5l2-2 3 3-2 3C7 14 2 9 1 3z" fill="#fff"/></svg><span>Phone<br>+41 44 555 01 90</span></div>
  <div class="contact-row"><svg width="16" height="16" viewBox="0 0 16 16"><path d="M1 7l14-6-5 14-2-6z" fill="#fff"/></svg><span>Email<br>hello@tiny-threaddays.ch</span></div>
</div>
<div class="abs foot-col" style="left:800px;width:270px">
  <h5>Newsletter Sign Up</h5>
  <p style="font-size:12px;line-height:18px">Subscribe to our newsletter to get the latest update to your inbox</p>
  <div class="email-field">Email address</div>
  <span class="btn btn-pink" style="padding:7px 28px">SUBSCRIBE</span>
</div>
<div class="abs copy center">© 2025 Tiny-ThreadDays. All Rights Reserved.</div>

</body>
</html>
```